Hunting club needs a new web design !

We need a new web design for our hunting club located in Poland, called "BORYNA". The club was founded in 1945. Colors that we would like to see in the project are the colors of the forest. The website should be built in such a way that all text elements can be changed to another language and can't be graphic.
"BORYNA" means - big, thick forest in which the game, small and big resides

Target Market(s)

hunters,

Industry/Entity Type

Hunting

Coding

Coded - Design and coding required

Number of Pages Required

5+ page

Font styles to use
Decorative

Colors

Designer to choose colors to be used in the design.

Requirements
Must have
• current date, calendar,
• must contain almost all materials from our current web page
• http://boryna-lasowiec.webnest.pl/
• new web address: borynalsw.pl
Nice to have
• current weather in three hunting regions that we allowed to hunt, or indicated by the visitor on the map placed on our web,
• actual phase of the moon, actual moon rising hour, actual moon set hour, actual sun rise hour, actual sun set hour, current weather in region (stalowa wola, poland)
• wood, forest, deers, boars,
Should not have
• mountain photos, modern look, white or bright backgrounds,

```html
<!DOCTYPE html>
<html lang="en">
<head>
<meta charset="utf-8">
<title>BORYNA Hunting Club</title>
<link href="https://fonts.googleapis.com/css2?family=Merriweather:wght@400;700&family=Poppins:wght@400;500&family=Open+Sans:wght@400;600&display=swap" rel="stylesheet">
<style>
:root{
  --green-light:#57d884;
  --green-deep:#009a00;
  --green-weather:#33c463;
  --forest-dark:#1d2a12;
  --forest-mid:#3d5a22;
  --text-dark:#333333;
  --text-mid:#6b6b6b;
  --line:#dddddd;
  --field:#e8e8e8;
  --white:#ffffff;
  --footer:#323232;
  --sun:#f7c600;
  --moon:#d6d6d6;
  --pin:#5a2a14;
}
*{margin:0;padding:0;box-sizing:border-box}
html,body{width:1200px;height:2575px;overflow:hidden;background:var(--white)}
body{position:relative;font-family:'Poppins',sans-serif;color:var(--text-dark)}
.abs{position:absolute}

/* hero */
.hero{left:0;top:0;width:1200px;height:565px;background:radial-gradient(ellipse at 50% 55%,#4e6e2c 0%,#2e4519 55%,#16220c 100%)}
.nav{left:0;top:0;width:1200px;height:46px}
.nav a{position:absolute;top:13px;color:var(--white);font-size:16px;font-weight:500;text-decoration:none;transform:translateX(-50%);font-family:'Open Sans',sans-serif}
.brand{left:0;top:190px;width:1200px;text-align:center;color:var(--white);font-family:'Merriweather',serif;font-weight:700;font-size:40px;letter-spacing:4px}
.brand .dot{display:inline-block;width:18px;height:18px;border-radius:50%;background:var(--white);margin-right:16px;vertical-align:middle}
.hero-title{left:0;top:345px;width:1200px;text-align:center;color:var(--white);font-family:'Merriweather',serif;font-weight:700;font-size:29px;line-height:68px}

/* intro */
.intro-title{left:96px;top:638px;width:560px;font-family:'Merriweather',serif;font-size:20px;line-height:42px;color:var(--text-dark)}
.intro-text{left:96px;top:740px;width:585px;font-size:12px;line-height:27px;color:var(--text-mid)}
.btn-solid{background:var(--green-light);color:var(--white);font-size:15px;font-weight:500;text-align:center}
.intro-btn{left:96px;top:870px;width:145px;height:38px;line-height:38px}

.moon-box{left:755px;top:630px;width:344px;height:301px;border:2px solid var(--line);background:var(--white)}
.moon-head{left:-2px;top:-2px;width:344px;height:53px;background:var(--green-deep);color:var(--white);font-size:22px;text-align:center;line-height:53px}
.moon-row{left:30px;width:290px;height:32px;font-size:15px;color:var(--text-dark)}
.moon-row span{position:absolute;left:0;top:6px}
.select{position:absolute;left:124px;top:0;width:200px;height:32px;background:var(--field);font-size:12px;padding:8px 16px}
.select::after{content:"";position:absolute;right:12px;top:13px;border:5px solid transparent;border-top-color:#777}
.moon-btn{left:31px;top:236px;width:282px;height:41px;line-height:41px;background:var(--green-deep);color:var(--white);font-size:15px;text-align:center}

/* band */
.band{left:0;top:998px;width:1200px;height:467px;background:linear-gradient(180deg,#4a5a2c 0%,#6f7a3a 45%,#3d4e24 100%)}
.cal{left:151px;top:1063px;width:436px;height:338px;background:var(--white)}
.cal-month{left:0;top:48px;width:436px;text-align:center;font-family:'Merriweather',serif;font-size:21px;color:var(--green-light)}
.cal-arrow{top:54px;width:14px;height:14px;border-left:3px solid var(--line);border-bottom:3px solid var(--line)}
.cal-grid{left:84px;top:112px;display:grid;grid-template-columns:repeat(7,38px);grid-auto-rows:40px;font-size:11px;color:var(--text-dark);text-align:center}
.cal-grid .dow{color:var(--green-light);font-size:10px}
.cal-grid div{display:flex;align-items:center;justify-content:center}
.cal-grid .today{background:#8fe2ac;color:var(--white);margin:8px 4px}
.check{left:587px;top:1063px;width:436px;height:338px;background:var(--green-light);color:var(--white)}
.check h3{position:absolute;left:40px;top:60px;font-size:16px;font-weight:500}
.check p{position:absolute;left:40px;top:100px;width:360px;font-size:11px;line-height:27px;text-align:justify}
.btn-outline{position:absolute;left:43px;top:252px;width:145px;height:40px;border:1px solid var(--white);line-height:38px;text-align:center;font-size:15px}

/* weather */
.weather{left:91px;top:1542px;width:1004px;height:568px;border:2px solid var(--line);background:var(--white)}
.weather-top{left:-2px;top:-2px;width:1004px;height:254px;background:var(--green-weather);color:var(--white)}
.notch{left:90px;top:-2px}
.w-day{left:56px;top:72px;font-family:'Merriweather',serif;font-size:32px}
.w-day small{font-size:21px;margin-left:10px}
.w-time{left:56px;top:120px;font-family:'Merriweather',serif;font-size:32px}
.w-place{left:56px;top:180px;font-family:'Merriweather',serif;font-size:23px}
.w-compass{left:596px;top:70px}
.w-speed{left:742px;top:100px;font-family:'Open Sans',sans-serif;font-size:37px}
.divider{left:0;top:415px;width:1000px;height:2px;background:var(--line)}
.cell{width:300px;height:130px}
.cell .clock{position:absolute;left:0;top:0}
.cell .dur{position:absolute;left:46px;top:6px;font-size:13px;color:var(--text-dark)}
.cell .label{position:absolute;left:0;top:50px;font-family:'Merriweather',serif;font-size:22px;line-height:36px;color:var(--text-mid)}
.cell .icon{position:absolute;left:200px;top:50px}

/* map */
.map{left:0;top:2193px;width:1200px;height:331px;background:linear-gradient(135deg,#e9e4d4 0%,#d9dfc6 45%,#e7dfcf 100%)}
.pin{position:absolute}
.map-tag{position:absolute;background:var(--green-deep);color:var(--white);font-family:'Merriweather',serif;font-weight:700;font-size:14px;height:38px;line-height:38px;padding:0 18px}
.footer{left:0;top:2524px;width:1200px;height:51px;background:var(--footer);color:#dddddd;font-size:11px;text-align:center;line-height:51px}
.footer .code{position:absolute;right:16px;top:0}
</style>
</head>
<body>

<section class="abs hero" role="img" aria-label="Photograph of a dense green forest with tall trees and mossy ground"></section>
<nav class="abs nav">
  <a href="#" style="left:185px">Home</a>
  <a href="#" style="left:350px">About Us</a>
  <a href="#" style="left:524px">Services</a>
  <a href="#" style="left:682px">Blog</a>
  <a href="#" style="left:838px">Gallery</a>
  <a href="#" style="left:1013px">Contact Us</a>
</nav>
<div class="abs brand"><span class="dot"></span>BORYNA</div>
<h1 class="abs hero-title">Helps Myelixwm And Friendly Hunters To Learn About<br>The Scope Of Our Activities And Problems</h1>

<h2 class="abs intro-title">The Beginning May Be Difficult, But We Know,<br>Over Time We'll Make It</h2>
<p class="abs intro-text">Lorem Ipsum is simply dummy text of the printing and typesetting industry. Lorem Ipsum has been the industry's standard dummy text ever since the 1500s, when an unknown printer took a galley of type and scrambled it to make a type specimen book. It has survived not only five centuries Lorem Ipsum is simply dummy text of the printing and typesetting industry.</p>
<div class="abs btn-solid intro-btn">Read More</div>

<aside class="abs moon-box">
  <div class="abs moon-head">Fazy Ksiezyca</div>
  <div class="abs moon-row" style="top:78px"><span>rok:</span><div class="select">2014</div></div>
  <div class="abs moon-row" style="top:130px"><span>miesiac:</span><div class="select"></div></div>
  <div class="abs moon-row" style="top:180px"><span>dzien:</span><div class="select"></div></div>
  <div class="abs moon-btn">POKAZ FAZY KSIEZYYCA</div>
</aside>

<section class="abs band" role="img" aria-label="Photograph of a pine forest with sunlit trunks"></section>
<div class="abs cal">
  <div class="abs cal-arrow" style="left:80px;transform:rotate(45deg)"></div>
  <div class="abs cal-month">August 2017</div>
  <div class="abs cal-arrow" style="left:340px;transform:rotate(-135deg)"></div>
  <div class="abs cal-grid">
    <div class="dow">S</div><div class="dow">M</div><div class="dow">T</div><div class="dow">W</div><div class="dow">T</div><div class="dow">F</div><div class="dow">S</div>
    <div>1</div><div>2</div><div>3</div><div>4</div><div>5</div><div>6</div><div>7</div>
    <div>8</div><div>9</div><div>10</div><div>11</div><div>12</div><div>13</div><div>14</div>
    <div>15</div><div>16</div><div>17</div><div class="today">18</div><div>19</div><div>20</div><div>21</div>
    <div>22</div><div>24</div><div>25</div><div>26</div><div>27</div><div>28</div><div>29</div>
  </div>
</div>
<div class="abs check">
  <h3>Check What We Do Now</h3>
  <p>Lorem Ipsum is simply dummy text of the printing and typesetting industry. Lorem Ipsum has been the industry's standard dummy text ever since the 1500s, when an unknown printer took a galley of type and scrambled it to make a type specimen book. It has survived not only five centuries</p>
  <div class="btn-outline">Read More &gt;&gt;</div>
</div>

<section class="abs weather">
  <div class="abs weather-top">
    <div class="abs w-day">Friday<small>18th Aug</small></div>
    <div class="abs w-time">6.00 am</div>
    <div class="abs w-place">Weather Condition In Stalowa Wola, Poland</div>
    <svg class="abs w-compass" width="130" height="130" viewBox="0 0 130 130">
      <circle cx="65" cy="65" r="38" fill="none" stroke="#fff" stroke-width="6"/>
      <path d="M84 46 L52 62 L64 66 L68 78 Z" fill="#fff"/>
      <g fill="#fff" font-family="Open Sans,sans-serif" font-weight="600" font-size="17" text-anchor="middle">
        <text x="65" y="18">N</text><text x="65" y="126">S</text><text x="12" y="71">W</text><text x="118" y="71">E</text>
      </g>
    </svg>
    <div class="abs w-speed">16-22 km/h</div>
  </div>
  <svg class="abs notch" width="74" height="24" viewBox="0 0 74 24"><path d="M0 0 L37 24 L74 0 Z" fill="#fff"/></svg>
  <div class="abs divider"></div>

  <div class="abs cell" style="left:43px;top:270px">
    <svg class="clock" width="32" height="32" viewBox="0 0 32 32"><rect x="2" y="2" width="28" height="28" rx="6" fill="none" stroke="var(--green-weather)" stroke-width="2"/><circle cx="16" cy="17" r="9" fill="none" stroke="var(--green-weather)" stroke-width="2"/><path d="M16 12v5h4" stroke="var(--green-weather)" stroke-width="2" fill="none"/></svg>
    <div class="dur">12 hr: 30 min</div>
    <div class="label">Actual Phase<br>Of The Moon</div>
    <svg class="icon" width="54" height="54" viewBox="0 0 54 54"><path d="M34 4 A24 24 0 1 0 50 38 A20 20 0 0 1 34 4Z" fill="var(--moon)"/></svg>
  </div>
  <div class="abs cell" style="left:386px;top:270px">
    <svg class="clock" width="32" height="32" viewBox="0 0 32 32"><rect x="2" y="2" width="28" height="28" rx="6" fill="none" stroke="var(--green-weather)" stroke-width="2"/><circle cx="16" cy="17" r="9" fill="none" stroke="var(--green-weather)" stroke-width="2"/><path d="M16 12v5h4" stroke="var(--green-weather)" stroke-width="2" fill="none"/></svg>
    <div class="dur">12 hr: 30 min</div>
    <div class="label">Actual Moon<br>Rising Hour</div>
    <svg class="icon" width="54" height="54" viewBox="0 0 54 54"><path d="M34 4 A24 24 0 1 0 50 38 A20 20 0 0 1 34 4Z" fill="var(--moon)"/></svg>
  </div>
  <div class="abs cell" style="left:721px;top:270px">
    <svg class="clock" width="32" height="32" viewBox="0 0 32 32"><rect x="2" y="2" width="28" height="28" rx="6" fill="none" stroke="var(--green-weather)" stroke-width="2"/><circle cx="16" cy="17" r="9" fill="none" stroke="var(--green-weather)" stroke-width="2"/><path d="M16 12v5h4" stroke="var(--green-weather)" stroke-width="2" fill="none"/></svg>
    <div class="dur">12 hr: 30 min</div>
    <div class="label">Actual Moon<br>Set Hour</div>
    <svg class="icon" width="54" height="54" viewBox="0 0 54 54"><path d="M34 4 A24 24 0 1 0 50 38 A20 20 0 0 1 34 4Z" fill="var(--moon)"/></svg>
  </div>

  <div class="abs cell" style="left:43px;top:430px">
    <svg class="clock" width="32" height="32" viewBox="0 0 32 32"><rect x="2" y="2" width="28" height="28" rx="6" fill="none" stroke="var(--green-weather)" stroke-width="2"/><circle cx="16" cy="17" r="9" fill="none" stroke="var(--green-weather)" stroke-width="2"/><path d="M16 12v5h4" stroke="var(--green-weather)" stroke-width="2" fill="none"/></svg>
    <div class="dur">06 hr: 30 min</div>
    <div class="label">Actual Phase<br>Of The Sun</div>
    <svg class="icon" width="58" height="58" viewBox="0 0 58 58"><circle cx="29" cy="29" r="13" fill="var(--sun)"/><g stroke="var(--sun)" stroke-width="4" stroke-linecap="round"><path d="M29 3v7M29 48v7M3 29h7M48 29h7M10.6 10.6l5 5M42.4 42.4l5 5M10.6 47.4l5-5M42.4 15.6l5-5"/></g></svg>
  </div>
  <div class="abs cell" style="left:386px;top:430px">
    <svg class="clock" width="32" height="32" viewBox="0 0 32 32"><rect x="2" y="2" width="28" height="28" rx="6" fill="none" stroke="var(--green-weather)" stroke-width="2"/><circle cx="16" cy="17" r="9" fill="none" stroke="var(--green-weather)" stroke-width="2"/><path d="M16 12v5h4" stroke="var(--green-weather)" stroke-width="2" fill="none"/></svg>
    <div class="dur">06 hr: 00 min</div>
    <div class="label">Actual Sun<br>Rising Hour</div>
    <svg class="icon" width="58" height="58" viewBox="0 0 58 58"><circle cx="29" cy="29" r="13" fill="var(--sun)"/><g stroke="var(--sun)" stroke-width="4" stroke-linecap="round"><path d="M29 3v7M29 48v7M3 29h7M48 29h7M10.6 10.6l5 5M42.4 42.4l5 5M10.6 47.4l5-5M42.4 15.6l5-5"/></g></svg>
  </div>
  <div class="abs cell" style="left:721px;top:430px">
    <svg class="clock" width="32" height="32" viewBox="0 0 32 32"><rect x="2" y="2" width="28" height="28" rx="6" fill="none" stroke="var(--green-weather)" stroke-width="2"/><circle cx="16" cy="17" r="9" fill="none" stroke="var(--green-weather)" stroke-width="2"/><path d="M16 12v5h4" stroke="var(--green-weather)" stroke-width="2" fill="none"/></svg>
    <div class="dur">06 hr: 00 min</div>
    <div class="label">Actual Sun<br>Set Hour</div>
    <svg class="icon" width="58" height="58" viewBox="0 0 58 58"><circle cx="29" cy="29" r="13" fill="var(--sun)"/><g stroke="var(--sun)" stroke-width="4" stroke-linecap="round"><path d="M29 3v7M29 48v7M3 29h7M48 29h7M10.6 10.6l5 5M42.4 42.4l5 5M10.6 47.4l5-5M42.4 15.6l5-5"/></g></svg>
  </div>
</section>

<section class="abs map" role="img" aria-label="Road map of Poland and neighbouring countries showing three hunting regions">
  <svg class="pin" style="left:240px;top:120px" width="32" height="50" viewBox="0 0 32 50"><circle cx="16" cy="16" r="13" fill="#fff" stroke="var(--pin)" stroke-width="4"/><path d="M16 29v20" stroke="var(--pin)" stroke-width="3"/></svg>
  <div class="map-tag" style="left:272px;top:155px">Hunting Red Deer</div>
  <svg class="pin" style="left:635px;top:200px" width="32" height="50" viewBox="0 0 32 50"><circle cx="16" cy="16" r="13" fill="#fff" stroke="var(--pin)" stroke-width="4"/><path d="M16 29v20" stroke="var(--pin)" stroke-width="3"/></svg>
  <div class="map-tag" style="left:658px;top:236px">Fallow deer</div>
  <svg class="pin" style="left:872px;top:68px" width="32" height="50" viewBox="0 0 32 50"><circle cx="16" cy="16" r="13" fill="#fff" stroke="var(--pin)" stroke-width="4"/><path d="M16 29v20" stroke="var(--pin)" stroke-width="3"/></svg>
  <div class="map-tag" style="left:905px;top:99px">Roebuck</div>
</section>

<footer class="abs footer">Copyright &copy; 2017 boryna- Lasowiec Webnest. All Rights Reserved.<span class="code">C12</span></footer>

</body>
</html>
```